Lurvik.no is a new website about pedagogical entrepreneurship. It's main target group is teachers. The Nordic Bureau for Digital Schooling and the National Office for Learning and Classrooms are leading the project.

The web page is meant to show examples of how different methods of entrepreneurship can be used pedagogical in a learning environment. The page will also support the user with examples of different teaching programs and other examples of best practice.

Pedagogical entrepreneurship is not about business and men in suits. It's a method for learning. The focus in the design should be on school, education and new ways of learning.

The final product should be motivating and engaging, but at the same time governmental and serious. We are not looking for something "flashy" and corporate-looking, but a moderate, task-focused and clean design that state quality.

We need designs for three pages:
1 - frontpage
2 - subpage ("Metoder og undervisningsopplegg")
3 - subpage ("Små-TOPP i Vassbygd")

The interaction design for these three pages will be uploaded as an attachment.

We would like you to find inspiration in the following websites:
- www.skapekraft.no
- www.giellu.no
- www.brightfernlab.com
- www.zyx.no
(more will be added)

Please use the attached logo, and feel free to use this as an inspiration for the rest of the design.

Target Market(s)

Teachers

Industry/Entity Type

Education

Requirements
Must have
• * Header with: Logo. Main navigation. Utility navigation. Search box.
* Footer
Should not have
• Images of men in suits.
Very strong graphical elements that stands out too much (we want it clean).

```html
<!DOCTYPE html>
<html lang="en">
<head>
<meta charset="utf-8">
<title>Lurvik.no – Pedagogical entrepreneurship</title>
<link href="https://fonts.googleapis.com/css2?family=Open+Sans:ital,wght@0,400;0,600;0,700;1,400;1,700&family=Arimo:wght@400;700&display=swap" rel="stylesheet">
<style>
:root{
  --navy:#0e4a78;
  --navy-deep:#0b3f67;
  --hero:#0f5283;
  --sky:#4fa8e0;
  --sky-soft:#5cb3ea;
  --ink:#1b1b1b;
  --title:#134f7f;
  --rule:#cfcfcf;
  --panel:#dadada;
  --white:#ffffff;
}
*{box-sizing:border-box;margin:0;padding:0}
html,body{width:956px;height:1200px;overflow:hidden;background:var(--white)}
body{position:relative;font-family:"Open Sans",sans-serif;color:var(--ink)}
a{color:inherit;text-decoration:none}
.abs{position:absolute}

/* utility bar */
.utility{position:absolute;top:0;left:0;width:956px;height:35px;background:var(--white)}
.utility-nav{position:absolute;top:10px;left:379px;display:flex;font-family:"Arimo",sans-serif;font-size:12px;color:#111}
.utility-nav a{padding:0 18px;border-left:1px solid #cfcfcf;line-height:16px}
.utility-nav a:first-child{padding-left:0;border-left:0}
.search{position:absolute;left:757px;top:7px;width:170px;height:20px;border:1px solid #9aa7b2;background:#fff}
.search svg{position:absolute;right:4px;top:3px}

/* header */
.masthead{position:absolute;top:35px;left:0;width:956px;height:87px;background:var(--navy);box-shadow:0 3px 6px rgba(0,0,0,.25);z-index:2}
.brand{position:absolute;left:30px;top:22px;display:flex;align-items:center;gap:14px;color:var(--white);font-weight:700;font-size:36px;letter-spacing:-.5px}
.brand-dot{width:40px;height:40px;border-radius:50%;background:var(--sky)}
.tagline{position:absolute;left:416px;top:15px;width:520px;color:var(--white);font-style:italic;font-weight:700;font-size:15.5px;line-height:20px}
.tagline a{font-style:normal;font-weight:400;font-size:13px;color:var(--sky-soft);font-family:"Arimo",sans-serif}

/* hero */
.hero{position:absolute;top:122px;left:0;width:956px;height:311px;background:linear-gradient(180deg,#0d4a78 0%,var(--hero) 40%,#0f5283 100%)}
.feature{position:absolute;top:0;width:260px}
.diamond{position:absolute;top:40px;width:135px;height:135px}
.diamond-tile{position:absolute;left:19px;top:19px;width:97px;height:97px;border-radius:20px;transform:rotate(45deg);background:linear-gradient(135deg,#ffffff,#d6d6d6);box-shadow:0 2px 6px rgba(0,0,0,.3)}
.diamond-art{position:absolute;left:35px;top:33px;width:66px;height:66px;border-radius:8px;background:linear-gradient(180deg,#e9e9e9,#9a9a9a)}
.feature-kicker{position:absolute;top:183px;font-style:italic;font-size:13px;color:var(--sky)}
.feature-title{position:absolute;top:203px;width:240px;font-weight:600;font-size:21px;line-height:25px;color:var(--white)}

/* get started */
.try-box{position:absolute;left:23px;top:441px;width:265px;height:224px;background:var(--panel);border:1px solid #b9b9b9}
.try-badge{position:absolute;left:12px;top:18px;width:28px;height:28px;border-radius:6px;background:linear-gradient(135deg,#fff,#cfcfcf)}
.try-title{position:absolute;left:51px;top:13px;font-weight:600;font-size:16.5px;line-height:20px;color:var(--title)}
.try-meter{position:absolute;left:79px;top:68px;width:102px;height:102px;border-radius:50%;background:radial-gradient(circle at 40% 40%,#3fa0d8,#2a5f7c 55%,#3a3a3a 75%,#8a8a8a)}
.try-button{position:absolute;left:30px;top:181px;width:202px;height:34px;border-radius:5px;background:linear-gradient(180deg,#ffffff,#e3e3e3);box-shadow:0 2px 3px rgba(0,0,0,.35);text-align:center;line-height:34px;font-weight:700;font-size:13px;color:#1d3550;letter-spacing:.3px}

.get-started{position:absolute;left:330px;top:454px;font-weight:600;font-size:17px;color:var(--title)}
.link-col{position:absolute;top:486px}
.link-col h3{font-weight:600;font-size:15.5px;color:#111;margin-bottom:6px}
.link-col li{list-style:none;font-size:12.5px;line-height:27px;color:#222}
.see-more{position:absolute;width:76px;height:22px;border-radius:3px;background:linear-gradient(180deg,#1e6aa0,#0b4470);box-shadow:0 2px 3px rgba(0,0,0,.3);color:#fff;font-size:9.5px;font-weight:700;text-align:center;line-height:22px}
.vrule{position:absolute;width:1px;background:var(--rule)}

/* inspiration */
.section-title{position:absolute;left:25px;top:692px;font-weight:600;font-size:17px;color:var(--title)}
.hrule{position:absolute;left:23px;width:905px;height:1px;background:var(--rule)}
.school{position:absolute;top:744px;width:150px;text-align:center}
.school-photo{width:150px;height:135px}
.school-name{margin-top:9px;font-weight:600;font-size:14.5px;line-height:17px;color:#111}
.school-place{font-size:12.5px;color:#222}
.chevron{position:absolute;top:796px}

/* footer */
.site-footer{position:absolute;top:964px;left:0;width:956px;height:236px;background:var(--navy);font-family:"Arimo",sans-serif}
.footer-col{position:absolute;top:23px}
.footer-col h4{font-weight:400;font-size:13px;color:var(--sky-soft);margin-bottom:5px}
.footer-col li{list-style:none;font-size:11px;line-height:19.5px;color:var(--white)}
.footer-col .more{font-size:8.5px;color:var(--sky-soft)}
.footer-brand{position:absolute;left:38px;top:173px;display:flex;align-items:center;gap:6px;color:var(--white);font-family:"Open Sans",sans-serif;font-weight:700;font-size:14px}
.footer-brand span.dot{width:18px;height:18px;border-radius:50%;background:var(--sky)}
.legal{position:absolute;left:105px;top:190px;font-size:10px;color:#2b80c2}
</style>
</head>
<body>

<header>
  <div class="utility">
    <nav class="utility-nav">
      <a href="#">Best practice schools</a>
      <a href="#">Lurvikometer</a>
      <a href="#">About Lurvik. no</a>
    </nav>
    <div class="search">
      <svg width="12" height="12" viewBox="0 0 12 12"><circle cx="5" cy="5" r="3.6" fill="none" stroke="#1c5a8a" stroke-width="1.6"/><line x1="7.6" y1="7.6" x2="11" y2="11" stroke="#1c5a8a" stroke-width="2"/></svg>
    </div>
  </div>

  <div class="masthead">
    <a class="brand" href="#"><span class="brand-dot"></span>Lurvik</a>
    <p class="tagline">Pedagogical entrepreneurship works. Lorem Ipsum is simply dummy text of the printing and typesetting industry. Lorem Ipsum has been the industry's standard dummy text..... <a href="#">Learn More</a></p>
  </div>
</header>

<section class="hero">
  <div class="feature" style="left:73px">
    <div class="diamond" style="left:33px"><div class="diamond-tile"></div><div class="diamond-art" role="img" aria-label="Laptop with an open book icon"></div></div>
    <p class="feature-kicker">Lrarn about what why and how!</p>
    <h2 class="feature-title">What is pedagogical entrepreneurship?</h2>
  </div>
  <div class="feature" style="left:361px">
    <div class="diamond" style="left:48px"><div class="diamond-tile"></div><div class="diamond-art" role="img" aria-label="Group of teachers icon"></div></div>
    <p class="feature-kicker">Plan your lessons!</p>
    <h2 class="feature-title">Methods and Teaching plans</h2>
  </div>
  <div class="feature" style="left:661px">
    <div class="diamond" style="left:36px"><div class="diamond-tile"></div>
      <svg class="abs" style="left:34px;top:34px" width="67" height="67" viewBox="0 0 67 67"><circle cx="33.5" cy="33.5" r="31" fill="#7a7a7a"/><circle cx="33.5" cy="33.5" r="27" fill="#5e5e5e"/><path d="M20 34 L30 44 L48 24" fill="none" stroke="#c9c9c9" stroke-width="6" stroke-linecap="round" stroke-linejoin="round"/></svg>
    </div>
    <p class="feature-kicker">Be inspired!</p>
    <h2 class="feature-title">Good examples/Best practice</h2>
  </div>
</section>

<main>
  <aside class="try-box">
    <div class="try-badge" role="img" aria-label="Small people icon"></div>
    <h2 class="try-title">Are You Working<br>entrepreneurship-like?</h2>
    <div class="try-meter" role="img" aria-label="Round meter icon with a pencil"></div>
    <a class="try-button" href="#">TRY THE LURVIKOMETER</a>
  </aside>

  <h2 class="get-started">Get Started!</h2>
  <div class="link-col" style="left:333px">
    <h3>Methods</h3>
    <ul><li>Cafe-Pedagogikk</li><li>Elevberift</li><li>Grundercamp</li><li>Story Line</li><li>Real</li></ul>
  </div>
  <a class="see-more" href="#" style="left:465px;top:641px">SEE MORE</a>
  <div class="vrule" style="left:620px;top:441px;height:225px"></div>
  <div class="link-col" style="left:642px">
    <h3>Teaching Plans</h3>
    <ul><li>Teaching plan title</li><li>Teaching plan title</li><li>Teaching plan title</li><li>Teaching plan title</li><li>Teaching plan title</li></ul>
  </div>
  <a class="see-more" href="#" style="left:769px;top:641px">SEE MORE</a>
  <div class="vrule" style="left:927px;top:441px;height:225px"></div>

  <h2 class="section-title">Inspiration</h2>
  <div class="hrule" style="top:722px"></div>

  <svg class="chevron" style="left:28px" width="22" height="32" viewBox="0 0 22 32"><path d="M18 3 L5 16 L18 29" fill="none" stroke="#d5d5d5" stroke-width="4"/></svg>
  <svg class="chevron" style="left:898px" width="22" height="32" viewBox="0 0 22 32"><path d="M4 3 L17 16 L4 29" fill="none" stroke="#d5d5d5" stroke-width="4"/></svg>

  <article class="school" style="left:67px">
    <div class="school-photo" role="img" aria-label="Photo of a school building with columns and lawn" style="background:linear-gradient(180deg,#8fb6e0 0%,#c9b9a4 45%,#8a6a52 65%,#5f8a3e 100%)"></div>
    <p class="school-name">Små-TOPP at</p><p class="school-place">Vassbygd School</p>
  </article>
  <div class="vrule" style="left:254px;top:744px;height:175px"></div>
  <article class="school" style="left:289px">
    <div class="school-photo" role="img" aria-label="Photo of a modern brick school building" style="background:linear-gradient(180deg,#5b8fd0 0%,#a9704f 40%,#8a5a40 65%,#9a8f86 100%)"></div>
    <p class="school-name">Små-TOPP at</p><p class="school-place">Vassbygd School</p>
  </article>
  <div class="vrule" style="left:476px;top:744px;height:175px"></div>
  <article class="school" style="left:512px">
    <div class="school-photo" role="img" aria-label="Photo of a school entrance with a clock tower" style="background:linear-gradient(180deg,#7fb0e4 0%,#b9d3ee 30%,#d8b07a 50%,#7a5a40 72%,#8a8a86 100%)"></div>
    <p class="school-name">Små-TOPP at</p><p class="school-place">Vassbygd School</p>
  </article>
  <div class="vrule" style="left:698px;top:744px;height:175px"></div>
  <article class="school" style="left:733px">
    <div class="school-photo" role="img" aria-label="Photo of a low school building behind a bare tree" style="background:linear-gradient(180deg,#9ec3ea 0%,#c4d8ea 45%,#8a5a48 65%,#5d8f36 78%,#4f7f2e 100%)"></div>
    <p class="school-name">Små-TOPP at</p><p class="school-place">Vassbygd School</p>
  </article>

  <div class="hrule" style="top:942px"></div>
</main>

<footer class="site-footer">
  <div class="footer-col" style="left:23px">
    <h4>Pedagogical Entrepreneurship</h4>
    <ul><li>what is pedagogical entrepreneurship?</li><li>Science</li><li>Best practice schools</li><li>Lurvikometer</li><li>About Lurvik. no</li></ul>
  </div>
  <div class="footer-col" style="left:334px">
    <h4>Methods</h4>
    <ul><li>Story Line</li><li>Real</li><li>Cafe-pedagogikk</li><li class="more">See more...</li></ul>
  </div>
  <div class="footer-col" style="left:540px">
    <h4>Teaching Plans</h4>
    <ul><li>&nbsp;Title</li><li>&nbsp;Title</li><li>&nbsp;Title</li><li>&nbsp;Title</li><li class="more">&nbsp;See more...</li></ul>
  </div>
  <div class="footer-col" style="left:744px">
    <h4>God Exempler</h4>
    <ul><li>&nbsp;Små-TOPP at Vassbygd School</li><li>&nbsp;Små-TOPP at Vassbygd School</li><li>&nbsp;Små-TOPP at Vassbygd School</li><li>&nbsp;Små-TOPP at Vassbygd School</li><li class="more">&nbsp;See more...</li></ul>
  </div>
  <div class="footer-brand"><span class="dot"></span>Lurvik</div>
  <p class="legal">© 2012 Lurvik - Terms of Service - Privacy Policy - Program Policies</p>
</footer>

</body>
</html>
```